Amber Reed Consulting Business Card

Hi Morwen. Thank you for your work on my coaching business card. I have another business which needs a new card. It is my counselling business. The best way to find out how to approach this project will be to go to my other website. www.amberreedconsulting.example.au and you will be able to see the colours scheme that I will require. White, Green and blue.

The tag line is Amber Reed Consulting So you can look forward to tomorrow. The clients are varied but mostly middle class Australian. The card is to show on it the same details as my other business card but with a different phone number. The tag lines are obviously different. The phone number is 5863 1427 The addresses are all the same.

Again simple, professional sophisticated is best.

Industry/Entity Type

Business

```html
<!DOCTYPE html>
<html lang="en">
<head>
<meta charset="utf-8">
<title>Amber Reed Consulting – Business Card</title>
<link rel="stylesheet" href="https://fonts.googleapis.com/css2?family=Exo+2:wght@400;500;600&display=swap">
<style>
  :root {
    --stage: #2a2a2c;
    --card-blue: #1f6fc2;
    --card-blue-light: #2f8fe2;
    --panel-white: #ffffff;
    --panel-shade: #eef1f4;
    --brand-navy: #2b3d8c;
    --brand-green: #3fa34d;
    --accent-orange: #f07a2a;
    --trim-red: #e2413a;
    --text-light: #ffffff;
    --text-dark: #222222;
  }
  * { box-sizing: border-box; margin: 0; padding: 0; }
  html, body { width: 1200px; height: 863px; overflow: hidden; }
  body {
    background: var(--stage);
    font-family: "Exo 2", sans-serif;
    display: flex;
    flex-direction: column;
    align-items: center;
    justify-content: center;
    gap: 40px;
  }
  .card {
    position: relative;
    width: 660px;
    height: 377px;
    background: linear-gradient(135deg, var(--card-blue) 0%, var(--card-blue-light) 60%, var(--card-blue) 100%);
    box-shadow: 0 10px 30px rgba(0,0,0,0.45);
    overflow: hidden;
  }
  .white-panel {
    position: absolute;
    background: radial-gradient(circle at 50% 45%, var(--panel-white) 0%, var(--panel-white) 55%, var(--panel-shade) 100%);
    display: flex;
    flex-direction: column;
    align-items: center;
    justify-content: center;
  }
  .card-front .white-panel { left: 60px; top: 16px; width: 540px; height: 345px; }
  .card-back .white-panel { left: 34px; top: 18px; width: 290px; height: 341px; }

  .brand-lockup {
    display: flex;
    align-items: center;
    gap: 12px;
  }
  .brand-dot {
    width: 22px; height: 22px;
    border-radius: 50%;
    background: var(--brand-green);
    flex: none;
  }
  .brand-name {
    font-weight: 600;
    color: var(--brand-navy);
    letter-spacing: 1.5px;
    white-space: nowrap;
  }
  .card-front .brand-name { font-size: 30px; }
  .card-back .brand-lockup { gap: 8px; }
  .card-back .brand-dot { width: 14px; height: 14px; }
  .card-back .brand-name { font-size: 18px; letter-spacing: 0.8px; }

  .tagline {
    margin-top: 10px;
    font-size: 15px;
    font-weight: 500;
    color: var(--brand-green);
    letter-spacing: 0.6px;
  }
  .front-website {
    margin-top: 24px;
    font-size: 17px;
    font-weight: 500;
    color: var(--text-dark);
    letter-spacing: 0.5px;
  }

  .trim-mark {
    position: absolute;
    height: 2px;
    width: 36px;
    background: var(--trim-red);
  }
  .card-front .trim-left { left: 0; top: 270px; }
  .card-front .trim-right { right: 0; top: 70px; }
  .card-back .trim-left { left: 0; top: 280px; width: 30px; }

  .contact-side {
    position: absolute;
    left: 342px;
    right: 22px;
    top: 34px;
    bottom: 24px;
    color: var(--text-light);
    text-align: right;
  }
  .holder-name {
    font-size: 27px;
    font-weight: 600;
    color: var(--accent-orange);
    letter-spacing: 1.5px;
    text-transform: uppercase;
    white-space: nowrap;
  }
  .holder-title {
    font-size: 15px;
    font-weight: 500;
    color: var(--accent-orange);
    letter-spacing: 2px;
    text-transform: uppercase;
    margin-top: 2px;
  }
  .divider {
    height: 2px;
    background: var(--accent-orange);
    margin: 14px 0 22px 0;
  }
  .contact-list { list-style: none; display: flex; flex-direction: column; gap: 16px; }
  .contact-row {
    display: flex;
    justify-content: flex-end;
    align-items: center;
    gap: 10px;
  }
  .contact-lines {
    font-size: 13px;
    line-height: 1.35;
    letter-spacing: 0.4px;
    white-space: nowrap;
  }
  .contact-lines.phone { font-size: 15px; letter-spacing: 1.4px; }
  .icon-tile {
    width: 30px; height: 30px;
    border-radius: 5px;
    background: var(--accent-orange);
    display: flex; align-items: center; justify-content: center;
    flex: none;
  }
  .icon-tile svg { width: 18px; height: 18px; }
</style>
</head>
<body>

  <section class="card card-front" aria-label="Card front">
    <div class="white-panel">
      <div class="brand-lockup">
        <span class="brand-dot"></span>
        <span class="brand-name">Amber Reed Consulting</span>
      </div>
      <p class="tagline">So you can look forward to tomorrow</p>
      <p class="front-website">www.amberreedconsulting.example.au</p>
    </div>
    <span class="trim-mark trim-left"></span>
    <span class="trim-mark trim-right"></span>
  </section>

  <section class="card card-back" aria-label="Card back">
    <div class="white-panel">
      <div class="brand-lockup">
        <span class="brand-dot"></span>
        <span class="brand-name">Amber Reed Consulting</span>
      </div>
    </div>
    <span class="trim-mark trim-left"></span>

    <div class="contact-side">
      <h1 class="holder-name">Daniel Forsyth</h1>
      <p class="holder-title">Financial Advisor</p>
      <div class="divider"></div>
      <ul class="contact-list">
        <li class="contact-row">
          <div class="contact-lines">Level 3, 12 Harbour Ln<br>Northbridge NSW 2063</div>
          <span class="icon-tile">
            <svg viewBox="0 0 24 24" aria-hidden="true"><path d="M12 2a7 7 0 0 0-7 7c0 5 7 13 7 13s7-8 7-13a7 7 0 0 0-7-7zm0 9.5A2.5 2.5 0 1 1 12 6.5a2.5 2.5 0 0 1 0 5z" fill="#fff"/></svg>
          </span>
        </li>
        <li class="contact-row">
          <div class="contact-lines phone">5863 1427<br>5863 1427</div>
          <span class="icon-tile">
            <svg viewBox="0 0 24 24" aria-hidden="true"><path d="M6.6 10.8a15.1 15.1 0 0 0 6.6 6.6l2.2-2.2a1 1 0 0 1 1-.25 11.4 11.4 0 0 0 3.6.57 1 1 0 0 1 1 1V20a1 1 0 0 1-1 1A17 17 0 0 1 3 4a1 1 0 0 1 1-1h3.5a1 1 0 0 1 1 1c0 1.25.2 2.45.57 3.57a1 1 0 0 1-.25 1z" fill="#fff"/></svg>
          </span>
        </li>
        <li class="contact-row">
          <div class="contact-lines">info@amberreed.example.au<br>www.amberreedconsulting.example.au</div>
          <span class="icon-tile">
            <svg viewBox="0 0 24 24" aria-hidden="true" fill="none" stroke="#fff" stroke-width="1.8"><circle cx="12" cy="12" r="9"/><path d="M3 12h18M12 3c2.8 3 2.8 15 0 18M12 3c-2.8 3-2.8 15 0 18"/></svg>
          </span>
        </li>
      </ul>
    </div>
  </section>

</body>
</html>
```